Website for Brisk Morning Rambles who develops hiking guides for easy to moderate hikes of up to 4 hours

Website for a company who creates hiking guides for State Parks and other tourist destinations. Looking for the ability to showcase various hiking destinations, our hiking guides, product favorites and blog with the ability to sell our hiking guides via the website shopping cart. Should feature photos from our hiking guides with the the ability to include photo thumbnails that can be expanded.

We need the ability to self manage the website - including ability to self update, add pages, graphics, etc.

While we want to have high quality photos we still want the pages to load quickly

Target Market(s)

People who enjoy nature and like to walk or hike for up to half a day on trails in a specific destination.
Adventure travelers who loves nature and the outdoors

Industry/Entity Type

Travel

Font styles to use
Sans Serif

Colors

Designer to choose colors to be used in the design.

Requirements
Must have
• We are looking for a fully operational WIX design for www.briskmorningrambles.example that has the following:
• 1. Menus - We want the ability to have multiple drop-down menus.
• 2. E-commerce – the ability to accept orders for books that we publish.
• 3. A form that can be filled out online to provide feedback on our hiking guides. (We will give the fields that need to be filled out.)
• 4. Pictures - Incorporates Professional Pictures– thumbnails that can be clicked to be larger, and pictures included with copy.
• 5. Logo – Our logo can be provided.
• 6. Domain Name - We already have the domain name briskmorningrambles.example
• 7. We want to be able to take your design and do our own changes via WIX.
• 8. The home page should have the ability to have scrolling photos – up to 10 images that can be easily updated.
• 9. Password protected pages that can only be accessed by a password.
• 10. We have a color palate that should be used for the site design
• 11. Six (6) major tabs
• #1 Home Page – Scrolling photos, general overview, hiking guide summary, other
• # 2 Destinations – Summary of all guides published, with sub-pages on each guide
• #3 Favorite products
• # 4 Blog – Blog index and all blogs
• #5 Photography
• #6 Contact us – form for feedback, links to other sites etc.
• We also need the ability to link to our Facebook and Instagram Accounts.
• Photos included as an example for our Home page.
• Please use the colors in our color palette provided as an attachment
Nice to have
• Examples of website designs we like as a reference
• https://www.roamingtheparkers.example
• https://www.torvalegrove.example/index.php
Should not have
• Colors that do not align with our color palette that is included as an attachment.

```html
<!DOCTYPE html>
<html lang="en">
<head>
<meta charset="utf-8">
<title>Brisk Morning Rambles</title>
<link rel="stylesheet" href="https://fonts.googleapis.com/css2?family=Montserrat:wght@400;500;600;700&display=swap">
<style>
:root{
  --blue:#2c5ba6;
  --orange:#d9542f;
  --orange-soft:#e48a52;
  --amber:#e59a3b;
  --maroon:#7b2a1e;
  --ink:#333;
  --muted:#555;
  --light:#ececec;
  --black:#111;
  --white:#fff;
}
*{box-sizing:border-box;margin:0;padding:0}
html,body{width:1200px;height:3725px;overflow:hidden}
body{font-family:"Montserrat",sans-serif;color:var(--ink);background:var(--white);position:relative}
.abs{position:absolute}
.center{text-align:center;left:0;width:1200px}

/* header */
.site-header{position:absolute;top:0;left:0;width:1200px;height:117px;background:var(--white);border-top:4px solid var(--blue);z-index:3}
.brand{position:absolute;left:111px;top:-2px;width:210px;height:209px;border-radius:50%;background:var(--white);z-index:4;display:flex;align-items:center;justify-content:center;text-align:center}
.brand-name{font-weight:700;color:var(--blue);font-size:25px;line-height:1.15;padding:40px 18px 0}
.main-nav{position:absolute;top:52px;left:0;width:1200px;font-size:12px;font-weight:600;color:#222;z-index:5}
.main-nav span{position:absolute;white-space:nowrap}
.main-nav .active{color:var(--orange)}
.caret{font-size:8px;margin-left:5px}

/* hero */
.hero{position:absolute;top:117px;left:0;width:1200px;height:745px;background:linear-gradient(180deg,#3f7fc8 0%,#8fb5de 25%,#c9d6e0 38%,#6b7b6a 55%,#5c7a3a 72%,#4d8fa0 88%,#3c7f93 100%)}
.hero-title{top:410px;font-size:74px;font-weight:700;color:var(--white)}
.hero-text{top:518px;font-size:19px;font-weight:500;color:var(--white);line-height:33px}
.btn{position:absolute;border-radius:40px;text-align:center;font-weight:600}
.btn-hero{left:494px;top:596px;width:212px;height:63px;line-height:63px;background:var(--orange);color:var(--white);font-size:21px}

/* section heading */
.section-title{font-size:40px;font-weight:500;color:var(--blue)}

/* products */
.product{position:absolute;width:200px;text-align:center}
.cover{width:150px;height:239px;margin:0 auto;border-radius:2px;box-shadow:6px 4px 0 #ddd}
.stars{color:var(--orange);font-size:14px;letter-spacing:2px;margin-top:28px}
.product-name{font-size:21px;font-weight:500;color:#444;margin-top:4px}
.price{font-size:21px;font-weight:500;color:var(--orange);margin-top:6px}
.btn-buy{position:relative;display:block;margin:24px auto 0;width:143px;height:49px;line-height:46px;border:2px solid var(--orange);border-radius:30px;color:var(--orange);font-size:16px;font-weight:500}

/* about */
.about{position:absolute;top:1580px;left:0;width:1200px;height:545px;background:linear-gradient(90deg,#7a6a55 0%,#b89070 40%,#e0b07a 60%,#c58658 80%,#6b6e73 100%)}
.about-panel{position:absolute;left:111px;top:0;width:412px;height:545px;background:rgba(217,100,45,.88);color:var(--white);padding:0 24px 0 37px}
.about-panel h2{font-weight:500;margin-top:66px;line-height:1.2;white-space:nowrap}
.about-panel .l1{font-size:33px;display:block}
.about-panel .l2{font-size:40px;display:block;letter-spacing:-0.5px}
.about-panel p{font-size:11px;line-height:26px;margin-top:30px;text-align:justify}
.btn-cart{left:148px;top:425px;width:173px;height:58px;line-height:58px;background:var(--blue);color:var(--white);font-size:17px}

/* blog */
.blog-intro{top:2290px;font-size:13px;color:var(--muted);line-height:27px}
.btn-read{left:519px;top:2365px;width:161px;height:54px;line-height:54px;background:var(--orange);color:var(--white);font-size:15px}
.blog-grid{position:absolute;top:2468px;left:111px;width:976px;height:445px;display:grid;grid-template-columns:repeat(4,244px);grid-template-rows:repeat(2,222.5px)}
.tile{position:relative;color:var(--white);text-align:center}
.tile h3{font-size:21px;font-weight:500;margin-top:30px}
.tile .date{font-size:16px;margin-top:12px}
.tile p{font-size:11.5px;line-height:25px;margin-top:10px;padding:0 12px}
.t-orange{background:var(--orange)}
.t-blue{background:var(--blue)}
.t-maroon{background:var(--maroon)}
.t-amber{background:var(--amber)}
.notch{position:absolute;width:0;height:0;border-left:12px solid transparent;border-right:12px solid transparent}

/* footer */
.footer{position:absolute;top:2988px;left:0;width:1200px;height:319px;background:var(--light)}
.fcol{position:absolute;top:44px}
.fcol h4{font-size:24px;font-weight:500;color:var(--blue)}
.fcol ul{list-style:none;margin-top:24px}
.fcol li{font-size:13px;color:#444;line-height:29px}
.fcol li::before{content:"»";margin-right:12px;color:#555}
.contact-item{position:relative;padding-left:32px;margin-top:22px}
.contact-item svg{position:absolute;left:0;top:2px}
.contact-item b{font-weight:500;font-size:16px;color:#333;display:block}
.contact-item small{font-size:11px;color:#444;line-height:19px;display:block}
.follow p{font-size:12px;line-height:25px;color:#444;margin-top:24px;width:225px}
.social{display:flex;gap:12px;margin-top:18px}
.social span{width:36px;height:36px;border:1.5px solid #555;border-radius:50%;display:block}

/* newsletter */
.newsletter{position:absolute;top:3307px;left:0;width:1200px;height:354px;background:var(--black);color:var(--white)}
.newsletter h4{position:absolute;top:54px;width:1200px;text-align:center;font-size:22px;font-weight:500}
.newsletter .sub{position:absolute;top:98px;width:1200px;text-align:center;font-size:13px}
.field{position:absolute;top:157px;width:276px;height:45px;background:var(--white);color:#333;font-size:13px;line-height:45px;padding-left:21px}
.btn-sub{left:503px;top:238px;width:194px;height:55px;line-height:55px;background:var(--orange);color:var(--white);font-size:16px;font-weight:500}

.copyright{position:absolute;top:3661px;left:0;width:1200px;height:64px;background:var(--blue);color:var(--white);font-size:12px;text-align:center;line-height:64px}
</style>
</head>
<body>

<header class="site-header">
  <nav class="main-nav">
    <span class="active" style="left:411px">HOME</span>
    <span style="left:489px">DESTINATIONS<span class="caret">▼</span></span>
    <span style="left:622px">FAVORITE PRODUCTS<span class="caret">▼</span></span>
    <span style="left:797px">BLOG</span>
    <span style="left:872px">PHOTOGRAPHY<span class="caret">▼</span></span>
    <span style="left:1009px">CONTACT US</span>
  </nav>
</header>
<div class="brand"><div class="brand-name">Brisk Morning Rambles</div></div>

<section class="hero" role="img" aria-label="Alpine lake with snowy peaks and a wooden cabin on a green hillside"></section>
<h1 class="abs center hero-title">Brisk Morning Rambles</h1>
<p class="abs center hero-text">Sed ut perspiciatis unde omnis iste natus error sit voluptatem<br>accusantium doloremque laudantium</p>
<a class="btn btn-hero">READ MORE</a>

<h2 class="abs center section-title" style="top:963px">Product Favorites</h2>

<svg class="abs" style="left:44px;top:1216px" width="30" height="130" viewBox="0 0 30 130"><polyline points="28,2 2,65 28,128" fill="none" stroke="#444" stroke-width="1.5"/></svg>
<svg class="abs" style="left:1126px;top:1216px" width="30" height="130" viewBox="0 0 30 130"><polyline points="2,2 28,65 2,128" fill="none" stroke="#444" stroke-width="1.5"/></svg>

<div class="product" style="left:127px;top:1077px">
  <div class="cover" role="img" aria-label="Hiking guide cover in blue and purple" style="background:linear-gradient(135deg,#1aa4e6,#3a4fd8 50%,#8a2bd6)"></div>
  <div class="stars">★★★★★</div><div class="product-name">Product Name</div><div class="price">$25.99</div><a class="btn-buy">BUY NOW</a>
</div>
<div class="product" style="left:374px;top:1077px">
  <div class="cover" role="img" aria-label="Hiking guide cover in green" style="background:linear-gradient(135deg,#1fa35a,#16c86a 50%,#5be04a)"></div>
  <div class="stars">★★★★★</div><div class="product-name">Product Name</div><div class="price">$25.99</div><a class="btn-buy">BUY NOW</a>
</div>
<div class="product" style="left:621px;top:1077px">
  <div class="cover" role="img" aria-label="Hiking guide cover in magenta" style="background:linear-gradient(135deg,#e8336a,#d40f8c 50%,#b01fa8)"></div>
  <div class="stars">★★★★★</div><div class="product-name">Product Name</div><div class="price">$25.99</div><a class="btn-buy">BUY NOW</a>
</div>
<div class="product" style="left:867px;top:1077px">
  <div class="cover" role="img" aria-label="Hiking guide cover in lime and yellow" style="background:linear-gradient(135deg,#7ad12a,#b6e01c 50%,#e2c412)"></div>
  <div class="stars">★★★★★</div><div class="product-name">Product Name</div><div class="price">$25.99</div><a class="btn-buy">BUY NOW</a>
</div>

<section class="about" role="img" aria-label="Hiker with raised arms on a grassy summit at sunrise">
  <div class="about-panel">
    <h2><span class="l1">About The</span><span class="l2">Hiking Products</span></h2>
    <p>Sed ut perspiciatis unde omnis iste natus error sit voluptatem accusantium doloremque laudantium, totam rem aperiam, eaque ipsa quae ab illo inventore veritatis et quasi architecto beatae vitae dicta sunt explicabo. Nemo enim ipsam voluptatem quia voluptas sit aspe matur aut odit aut fugit, sed quia consequuntur magni dolores eos qui ratione voluptatem</p>
  </div>
  <a class="btn btn-cart">ADD TO CART</a>
</section>

<h2 class="abs center section-title" style="top:2218px">Latest Blog</h2>
<p class="abs center blog-intro">Sed ut perspiciatis unde omnis iste natus error sit voluptatem accusantium doloremque laudantium, totam rem<br>inventore veritatis et quasi architecto beatae vitae dicta sunt explicabo.</p>
<a class="btn btn-read">READ MORE</a>

<section class="blog-grid">
  <div class="tile" role="img" aria-label="Hiker overlooking a mountain lake" style="background:linear-gradient(180deg,#8fb0cf,#4d6f86 55%,#3d5a3a)"></div>
  <div class="tile t-orange"><h3>Sed ut perspiciatis</h3><div class="date">22 July 2019</div><p>Nemo enim ipsam voluptatem quia voluptas sit aspernatur aut odit aut fugit, sed quia consequuntur magni dolores eos qui ratione</p></div>
  <div class="tile" role="img" aria-label="Group of hikers on an autumn forest trail" style="background:linear-gradient(180deg,#b9803e,#8a5a2e 60%,#6a4a2a)"></div>
  <div class="tile t-blue"><h3>Sed ut perspiciatis</h3><div class="date">22 July 2019</div><p>Nemo enim ipsam voluptatem quia voluptas sit aspernatur aut odit aut fugit, sed quia consequuntur magni dolores eos qui ratione</p></div>
  <div class="tile t-maroon"><h3>Sed ut perspiciatis</h3><div class="date">22 July 2019</div><p>Nemo enim ipsam voluptatem quia voluptas sit aspernatur aut odit aut fugit, sed quia consequuntur magni dolores eos qui ratione</p></div>
  <div class="tile" role="img" aria-label="Hand holding a brass compass in a forest" style="background:linear-gradient(135deg,#3d6a7a,#6b8a8a 50%,#a47a3e)"></div>
  <div class="tile t-amber"><h3>Sed ut perspiciatis</h3><div class="date">22 July 2019</div><p>Nemo enim ipsam voluptatem quia voluptas sit aspernatur aut odit aut fugit, sed quia consequuntur magni dolores eos qui ratione</p></div>
  <div class="tile" role="img" aria-label="Hikers with trekking poles on a green woodland path" style="background:linear-gradient(180deg,#6f8e46,#4f7a3a 55%,#3e5a6a)"></div>
</section>
<div class="notch" style="left:215px;top:2681px;border-bottom:12px solid var(--maroon)"></div>
<div class="notch" style="left:956px;top:2690px;border-top:12px solid var(--blue)"></div>

<footer class="footer">
  <div class="fcol" style="left:111px">
    <h4>Quick Links</h4>
    <ul><li>Home</li><li>Destinations</li><li>Favorite products</li><li>Blog</li><li>Photography</li><li>Contact us</li></ul>
  </div>
  <div class="fcol" style="left:357px">
    <h4>Info</h4>
    <ul><li>Sed ut perspiciatis</li><li>Unde omnis iste</li><li>Natus error sit</li><li>Voluptatem</li><li>Accusantium</li><li>doloremque</li></ul>
  </div>
  <div class="fcol" style="left:600px;width:230px">
    <h4>Contact Us</h4>
    <div class="contact-item"><svg width="12" height="16" viewBox="0 0 12 16"><path d="M6 0a6 6 0 0 0-6 6c0 4.5 6 10 6 10s6-5.5 6-10a6 6 0 0 0-6-6zm0 8.5A2.5 2.5 0 1 1 6 3.5a2.5 2.5 0 0 1 0 5z" fill="#333"/></svg><b>Address :</b><small>#15 Lorem Ipsum Dummy Text<br>Lorem Dummy</small></div>
    <div class="contact-item"><svg width="14" height="14" viewBox="0 0 14 14"><path d="M3 0l2.5 3-1.5 2c1 2 3 4 5 5l2-1.5 3 2.5-1.5 2.5C6 13.5.5 8 .5 1.5z" fill="#333"/></svg><b>Phone :</b><small>000-555-0148</small></div>
    <div class="contact-item"><svg width="15" height="11" viewBox="0 0 15 11"><rect width="15" height="11" fill="#333"/><polyline points="0,0 7.5,6 15,0" fill="none" stroke="#ececec" stroke-width="1.2"/></svg><b>Email :</b><small>info@briskmorningrambles.example</small></div>
  </div>
  <div class="fcol follow" style="left:870px">
    <h4>Follow Us</h4>
    <p>Sed ut perspiciatis unde omnis iste natus error sit voluptatem accusan tium doloremque laudantium</p>
    <div class="social"><span role="img" aria-label="Social profile link"></span><span role="img" aria-label="Photo profile link"></span></div>
  </div>
</footer>

<section class="newsletter">
  <h4>SIGN UP FOR OUR EMAIL NEWSLETTER</h4>
  <p class="sub">Sed ut perspiciatis unde omnis iste natus error sit voluptatem accusantium doloremque laudantium</p>
  <div class="field" style="left:159px">First Name :</div>
  <div class="field" style="left:462px">Last Name :</div>
  <div class="field" style="left:765px">Email :</div>
  <a class="btn btn-sub">SUBSCRIBE</a>
</section>

<div class="copyright">Copyrights © 2019 Brisk Morning Rambles.All Rights Reserved</div>

</body>
</html>
```